I need a business card design for a new business based in South West Australia.
I specialize in residential window cleaning & general handyman maintenance.

Dale Marsh - 412 SILVER HAWK DETAILING
- Window Cleaning
- House Maintenance

```html
<!DOCTYPE html>
<html lang="en">
<head>
<meta charset="utf-8">
<title>Silver Hawk Detailing – Business Card</title>
<link rel="stylesheet" href="https://fonts.googleapis.com/css2?family=Open+Sans:wght@400;600;700&display=swap">
<style>
  :root {
    --stage: #000000;
    --card: #ffffff;
    --brand-orange: #f5a300;
    --tag-orange: #ef7412;
    --ink: #1c1c1c;
    --ghost-light: #f4f4f4;
    --ghost-dark: #e2e2e2;
  }
  html, body {
    margin: 0;
    padding: 0;
    width: 1200px;
    height: 900px;
    overflow: hidden;
    background: var(--stage);
  }
  .canvas {
    position: relative;
    width: 1200px;
    height: 900px;
    background: var(--stage);
  }
  .card {
    position: absolute;
    top: 275px;
    width: 477px;
    height: 294px;
    background: var(--card);
    overflow: hidden;
    font-family: "Open Sans", Arial, sans-serif;
  }
  .card--front {
    left: 116px;
    border-radius: 0 52px 0 52px;
  }
  .card--back {
    left: 622px;
    border-radius: 52px 0 52px 0;
  }
  .brand-name {
    position: absolute;
    margin: 0;
    font-family: "Open Sans", Arial, sans-serif;
    font-weight: 600;
    font-size: 19px;
    line-height: 1;
    color: var(--brand-orange);
    white-space: nowrap;
    letter-spacing: 0.3px;
  }
  .brand-tagline {
    position: absolute;
    margin: 0;
    font-family: "Open Sans", Arial, sans-serif;
    font-weight: 700;
    font-size: 9px;
    line-height: 1;
    color: var(--tag-orange);
    white-space: nowrap;
    letter-spacing: 0.5px;
  }
  .brand-mark {
    position: absolute;
    left: 128px;
    top: 30px;
    width: 34px;
    height: 34px;
    background: var(--brand-orange);
    border-radius: 3px;
  }
  .card--front .brand-name { left: 0; width: 292px; top: 101px; text-align: center; }
  .card--front .brand-tagline { left: 0; width: 292px; top: 127px; text-align: center; }
  .card--back .brand-name { right: 24px; top: 40px; text-align: right; }
  .card--back .brand-tagline { right: 26px; top: 66px; text-align: right; }

  .person {
    position: absolute;
    right: 19px;
    top: 116px;
    text-align: right;
  }
  .person__name {
    margin: 0;
    font-weight: 600;
    font-size: 18.5px;
    line-height: 1.1;
    color: var(--brand-orange);
  }
  .person__role {
    margin: 2px 0 0;
    font-size: 13px;
    color: var(--ink);
  }
  .contact-list {
    position: absolute;
    right: 22px;
    top: 173px;
    margin: 0;
    padding: 0;
    list-style: none;
  }
  .contact-list li {
    display: flex;
    justify-content: flex-end;
    align-items: center;
    gap: 6px;
    height: 20px;
    font-size: 13px;
    color: var(--ink);
  }
  .contact-icon {
    width: 14px;
    height: 14px;
    flex: none;
  }
  .ghost-panel {
    position: absolute;
    left: 0;
    top: 0;
    width: 215px;
    height: 294px;
    background: linear-gradient(90deg, var(--ghost-dark) 0%, var(--ghost-light) 70%, var(--card) 100%);
    border-radius: 52px 0 0 0;
  }
</style>
</head>
<body>
<main class="canvas">

  <section class="card card--front" aria-label="Card front">
    <span class="brand-mark" aria-hidden="true"></span>
    <h1 class="brand-name">SILVER HAWK DETAILING</h1>
    <p class="brand-tagline">RESIDENTIAL WINDOWS &amp; HANDYMAN CARE</p>

    <div class="person">
      <p class="person__name">Dale Marsh</p>
      <p class="person__role">Managing Director</p>
    </div>

    <ul class="contact-list">
      <li>055-218-4630
        <svg class="contact-icon" viewBox="0 0 14 14" aria-label="Phone">
          <rect width="14" height="14" rx="2" fill="var(--brand-orange)"/>
          <path d="M3 5.5c0-1.5 8-1.5 8 0v1h-2v-1h-4v1H3z M4 7h6l1 4H3z" fill="#fff"/>
        </svg>
      </li>
      <li>089-731-2254
        <svg class="contact-icon" viewBox="0 0 14 14" aria-label="Fax">
          <rect width="14" height="14" rx="2" fill="var(--brand-orange)"/>
          <rect x="4" y="3" width="6" height="3" fill="#fff"/>
          <rect x="3" y="6.5" width="8" height="4.5" rx="1" fill="#fff"/>
        </svg>
      </li>
      <li>041-675-9382
        <svg class="contact-icon" viewBox="0 0 14 14" aria-label="Mobile">
          <rect width="14" height="14" rx="2" fill="var(--brand-orange)"/>
          <rect x="4.5" y="2.5" width="5" height="9" rx="1" fill="none" stroke="#fff" stroke-width="1.2"/>
        </svg>
      </li>
      <li>info@silverhawkdetailing.com
        <svg class="contact-icon" viewBox="0 0 14 14" aria-label="Email">
          <rect width="14" height="14" rx="2" fill="var(--brand-orange)"/>
          <rect x="3" y="4" width="8" height="6" fill="#fff"/>
          <path d="M3 4l4 3.2L11 4" fill="none" stroke="var(--brand-orange)" stroke-width="1"/>
        </svg>
      </li>
      <li>www.silverhawkdetailing.com
        <svg class="contact-icon" viewBox="0 0 14 14" aria-label="Website">
          <rect width="14" height="14" rx="2" fill="var(--brand-orange)"/>
          <path d="M5.5 8.5l3-3 M6 5l1-1a1.8 1.8 0 0 1 3 3l-1 1 M8 9l-1 1a1.8 1.8 0 0 1-3-3l1-1" fill="none" stroke="#fff" stroke-width="1.2" stroke-linecap="round"/>
        </svg>
      </li>
    </ul>
  </section>

  <section class="card card--back" aria-label="Card back">
    <div class="ghost-panel" role="img" aria-label="Large faint embossed brand symbol"></div>
    <h2 class="brand-name">SILVER HAWK DETAILING</h2>
    <p class="brand-tagline">RESIDENTIAL WINDOWS &amp; HANDYMAN CARE</p>
  </section>

</main>
</body>
</html>
```